Brookvale Estates LLC stationary for a real estate property management company.

Create stationary (letterhead, envelopes, business cards) using Brookvale Estates LLC logo as primary creative element. Stationary design needs to be horizontal, leaving as much space as possible for correspondence copy. See attached Creative Brief and past stationary files for details.

Target Market(s)

Prospective apartment residents and current residents, vendors, and government agencies.

Industry/Entity Type

Property Management

Contact Information for Business Card

Business card employee title: Property Manager. Should include address, phone, fax, email, website, slogan, and Brookvale Estates logo.

Font styles to use
Sans Serif

Colors
0592cd
000000

Requirements
Must have
• Tone should be conservative, institutional, business (i.e. banking, finance, real estate). Must include: address, phone, fax, website, and slogan (see attached Creative Brief). Should be a horizontal design, leaving as much room as possible for letter correspondence copy.
Nice to have
• Please use an Arial or Helvetica style font.
Should not have
• Letterhead layout should leave as much room as possible for copy.

```html
<!DOCTYPE html>
<html lang="en">
<head>
<meta charset="utf-8">
<title>Brookvale Estates LLC — Business Card</title>
<link href="https://fonts.googleapis.com/css2?family=Arimo:wght@400;700&display=swap" rel="stylesheet">
<style>
  :root {
    --backdrop: #262626;
    --card-white: #f6f6f6;
    --brand-blue: #0a6fae;
    --brand-blue-light: #1ab8ec;
    --brand-blue-deep: #0962a0;
    --swoosh-grey: #555555;
    --text-grey: #4a4a4a;
    --divider: #bdbdbd;
    --white: #ffffff;
  }
  * { margin: 0; padding: 0; box-sizing: border-box; }
  html, body { width: 1200px; height: 960px; overflow: hidden; }
  body {
    background: var(--backdrop);
    font-family: "Arimo", Arial, sans-serif;
    position: relative;
  }
  .card {
    position: absolute;
    width: 600px;
    height: 342px;
    overflow: hidden;
  }
  .card-front { left: 302px; top: 129px; background: var(--card-white); }
  .card-back {
    left: 299px; top: 488px;
    background: linear-gradient(135deg, var(--brand-blue-light) 0%, var(--brand-blue) 45%, var(--brand-blue-deep) 100%);
  }
  .corner-curves { position: absolute; inset: 0; }
  .brand-name {
    position: absolute;
    left: 48px; top: 148px;
    width: 240px;
    font-size: 24px; font-weight: 700;
    line-height: 28px;
    color: var(--brand-blue);
  }
  .divider {
    position: absolute;
    left: 307px; top: 96px;
    width: 2px; height: 174px;
    background: var(--divider);
  }
  .contact { position: absolute; left: 330px; top: 94px; color: var(--text-grey); }
  .person-name { font-size: 21px; font-weight: 700; color: var(--brand-blue); line-height: 26px; }
  .person-title { font-size: 15px; line-height: 20px; margin-bottom: 6px; }
  .address { font-size: 14px; line-height: 18px; margin-bottom: 8px; }
  .contact-list { list-style: none; font-size: 14px; line-height: 19px; }
  .contact-list li { display: flex; align-items: center; gap: 8px; }
  .contact-list svg { width: 14px; height: 14px; fill: var(--brand-blue); flex: none; }
  .back-name {
    position: absolute; left: 0; right: 0; top: 140px;
    text-align: center;
    font-size: 34px; font-weight: 700;
    color: var(--white);
  }
  .slogan {
    position: absolute; left: 0; right: 0; top: 288px;
    text-align: center;
    font-size: 16px; font-weight: 700;
    color: var(--white);
  }
</style>
</head>
<body>
  <section class="card card-front">
    <svg class="corner-curves" viewBox="0 0 600 342" width="600" height="342" aria-hidden="true">
      <path d="M466,0 Q578,22 600,136 L600,0 Z" fill="var(--brand-blue)"/>
      <path d="M466,0 Q572,26 597,132" fill="none" stroke="var(--swoosh-grey)" stroke-width="4"/>
      <path d="M0,209 Q22,322 135,342 L0,342 Z" fill="var(--brand-blue)"/>
      <path d="M3,205 Q28,318 136,342" fill="none" stroke="var(--swoosh-grey)" stroke-width="4"/>
    </svg>

    <div class="brand-name">Brookvale Estates<br>LLC</div>
    <div class="divider"></div>

    <div class="contact">
      <div class="person-name">DANIEL WHITFORD</div>
      <div class="person-title">Property Manager</div>
      <div class="address">2750 Harbor Ridge Drive #B210<br>Lakeview, CA 90412</div>
      <ul class="contact-list">
        <li>
          <svg viewBox="0 0 24 24"><path d="M6.6 10.8a15.1 15.1 0 0 0 6.6 6.6l2.2-2.2c.3-.3.7-.4 1-.2 1.1.4 2.3.6 3.6.6.6 0 1 .4 1 1V20c0 .6-.4 1-1 1A17 17 0 0 1 3 4c0-.6.4-1 1-1h3.5c.6 0 1 .4 1 1 0 1.3.2 2.5.6 3.6.1.3 0 .7-.2 1z"/></svg>
          555-314-7720
        </li>
        <li>
          <svg viewBox="0 0 24 24"><path d="M6 2h12v6H6zM3 9h18a1 1 0 0 1 1 1v8h-4v4H6v-4H2v-8a1 1 0 0 1 1-1zm5 8v3h8v-3z"/></svg>
          555-314-7721
        </li>
        <li>
          <svg viewBox="0 0 24 24"><path d="M2 5h20v14H2zm2 2v.5l8 5 8-5V7z"/></svg>
          daniel@brookvaleestates.us
        </li>
        <li>
          <svg viewBox="0 0 24 24"><circle cx="12" cy="12" r="10"/></svg>
          www.brookvaleestates.us
        </li>
      </ul>
    </div>
  </section>

  <section class="card card-back">
    <div class="back-name">Brookvale Estates</div>
    <div class="slogan">Multifamily Property Management</div>
  </section>
</body>
</html>
```